4th Generation Family Business Needs a New Card Design!

We are a family owned 4th Generation company. We are based in the Sydney, Australia area and we are desperately in need of a more modern and classy card. We are monumental masons who design, supply & erect lasting memorials throughout cemeteries in Sydney. Our customers are normally in a period of grieving. I have attached logo files that will need to be implemented on the card. Company was established 1935. Australian Owned and Operated. Card needs to be designed to PIXO.com specification.

Target Market(s)

Our target market is based upon people that a grieving for family members that have passed away. We also deal with alot of companies that own and operate cemeteries.

Industry/Entity Type

Business

Contact Information for Business Card

Simon Harcourt, Operations Manager, 0417293086, simon@harcourtmemorials.com.au
Lewis Harcourt, Director, 0491630572, lewis@harcourtmemorials.com.au
Phone # 02 9561 3048
Website: www.harcourtmemorials.com.au
Address: Suite 17, 8 Palfrey Lane, West Carlow, Sydney NSW 2156

Font styles to use
Serif
Decorative
Script

Requirements
Must have
• Would like to see the logo nicely implemented with a modern design. Embossed lettering would be a nice additive.

```html
<!DOCTYPE html>
<html lang="en">
<head>
<meta charset="utf-8">
<title>Harcourt Memorials — Business Card</title>
<link href="https://fonts.googleapis.com/css2?family=Cinzel:wght@400;600&family=Gelasio:wght@400&display=swap" rel="stylesheet">
<style>
  :root {
    --page: #e9e6e2;
    --card-black: #1b1b1c;
    --emboss-grey: #2c2c2e;
    --paper: #f7f7f6;
    --ink: #1c1c1c;
    --ink-soft: #3a3a3a;
    --gold: #e1b526;
    --rule: #d6d6d6;
    --white: #ffffff;
  }
  * { box-sizing: border-box; margin: 0; padding: 0; }
  html, body {
    width: 1200px; height: 716px; overflow: hidden;
    background: var(--page);
  }
  .stage { position: relative; width: 1200px; height: 716px; }

  .card {
    position: absolute; top: 199px;
    width: 520px; height: 318px;
    overflow: hidden;
    box-shadow: 0 2px 6px rgba(0,0,0,.18);
  }

  /* Back of card */
  .card-back { left: 50px; background: var(--card-black); }
  .card-back .brand-name {
    position: absolute; inset: 0;
    display: flex; align-items: center; justify-content: center;
    font-family: "Cinzel", serif; font-weight: 600;
    font-size: 34px; letter-spacing: 3px;
    color: var(--emboss-grey);
  }

  /* Front of card */
  .card-front { left: 630px; background: var(--paper); }

  .brand {
    position: absolute; left: 20px; top: 95px; width: 185px;
    display: flex; flex-direction: column; align-items: center; gap: 10px;
  }
  .brand-mark { width: 16px; height: 16px; background: var(--gold); }
  .brand .brand-name {
    font-family: "Cinzel", serif; font-weight: 600;
    font-size: 21px; letter-spacing: 1px; color: var(--ink);
    text-align: center; line-height: 1.15;
  }

  .divider {
    position: absolute; left: 215px; top: 45px;
    width: 1px; height: 190px; background: var(--rule);
  }

  .person { position: absolute; left: 240px; top: 62px; }
  .person-name {
    font-family: "Cinzel", serif; font-weight: 600;
    font-size: 20px; letter-spacing: 1px; color: var(--ink);
  }
  .person-title {
    font-family: "Gelasio", serif; font-size: 11px;
    color: var(--ink-soft); margin-top: 2px;
  }

  .contact-list {
    list-style: none; margin-top: 12px;
    font-family: "Gelasio", serif; font-size: 12.5px;
    color: var(--ink); line-height: 17px;
  }
  .contact-list li { display: flex; align-items: center; gap: 6px; }
  .contact-list .icon { width: 10px; height: 10px; flex: none; fill: var(--gold); }
  .contact-list .address { padding-left: 0; }

  .footer-bands { position: absolute; left: 0; bottom: 0; width: 520px; height: 50px; }
  .website {
    position: absolute; right: 28px; bottom: 14px;
    font-family: "Gelasio", serif; font-size: 12.5px;
    color: var(--white); letter-spacing: .3px;
  }
</style>
</head>
<body>
<main class="stage">

  <section class="card card-back" aria-label="Card back">
    <div class="brand-name">HARCOURT</div>
  </section>

  <section class="card card-front" aria-label="Card front">
    <div class="brand">
      <span class="brand-mark"></span>
      <div class="brand-name">HARCOURT<br>MEMORIALS</div>
    </div>

    <div class="divider"></div>

    <div class="person">
      <h1 class="person-name">SIMON HARCOURT</h1>
      <p class="person-title">Operations Manager</p>

      <ul class="contact-list">
        <li>
          <svg class="icon" viewBox="0 0 10 10" aria-hidden="true"><path d="M2 0.5 L3.8 2.6 L2.9 3.6 Q4 6 6.4 7.1 L7.4 6.2 L9.5 8 L8 9.5 Q3.5 9 0.5 2 Z"/></svg>
          0491630572
        </li>
        <li>
          <svg class="icon" viewBox="0 0 10 10" aria-hidden="true"><rect x="0.5" y="3" width="9" height="6" rx="1"/><rect x="1.5" y="0.8" width="7" height="2" rx="1"/></svg>
          02 9561 3048
        </li>
        <li>
          <svg class="icon" viewBox="0 0 10 10" aria-hidden="true"><rect x="0.5" y="2" width="9" height="6.5"/><path d="M0.8 2.3 L5 5.6 L9.2 2.3" fill="none" stroke="#f7f7f6" stroke-width="0.9"/></svg>
          lewis@harcourtmemorials.com.au
        </li>
        <li class="address">Suite 17, 8 Palfrey Lane,</li>
        <li class="address">West Carlow, Sydney NSW 2156</li>
      </ul>
    </div>

    <svg class="footer-bands" viewBox="0 0 520 50" aria-hidden="true">
      <polygon points="0,16 232,16 232,50 0,50" fill="var(--gold)"/>
      <polygon points="205,50 236,0 520,0 520,50" fill="var(--card-black)"/>
    </svg>
    <p class="website">www.harcourtmemorials.com.au</p>
  </section>

</main>
</body>
</html>
```